Holistic Health Coach needs a catchy and creative flyer

I need an eye-catching and convincing DL sized flyer for my new health coaching business. I provide advice and regular coaching to people on health, fitness and lifestyle issues.

I want these flyers to create awareness of my business as well as providing some information about what I do and the services that I can provide. I also want the flyers to have a strong and clear call-to-action so they can contact me.

I have provided some photos myself to be used in the flyer if necessary. I have also provided my logo. My Business name is called "Bright Path Notes" however I want to market myself as a " Qualified Holistic Health Coach".

Target Market(s)

Men and Women of all ages who are trying to improve their health and fitness

Industry/Entity Type

Health And Wellness

Font styles to use
Sans Serif

Requirements
Must have
• My Business is called "Bright Path Notes" (as seen in attached logo) but I would like the main marketing message of the flyer to be focused as " Qualified Holistic Health Coach" .
• The Flyer should be DL size.
• Strong call to action
• Catchy and memorable design- as I am a new business I want this to capture people's attention.
• Please see attached document for page content.
Nice to have
• I have also included some recent pictures of myself to be incorporated in the flyer, if appropriate.

```html
<!DOCTYPE html>
<html lang="en">
<head>
<meta charset="utf-8">
<title>Bright Path Notes – Holistic Health Coach Flyer</title>
<link rel="stylesheet" href="https://fonts.googleapis.com/css2?family=Amatic+SC:wght@700&family=Lato:wght@400;700;900&display=swap">
<style>
  :root {
    --page-bg: #e9e9e8;
    --paper: #ececeb;
    --paper-dark: #d6d6d5;
    --ink: #1d1d1d;
    --ink-soft: #3a3a3a;
    --green: #3a9a3c;
    --lime: #9ccc2a;
    --band: #1f1f1f;
    --tick: #c8202a;
    --white: #ffffff;
  }
  * { box-sizing: border-box; margin: 0; padding: 0; }
  html, body { width: 1200px; height: 1141px; overflow: hidden; }
  body { background: var(--page-bg); font-family: "Lato", Arial, sans-serif; color: var(--ink); position: relative; }

  .flyer {
    position: absolute; top: 50px; width: 520px; height: 1040px; overflow: hidden;
    background: radial-gradient(ellipse at 60% 40%, var(--paper) 0%, #e2e2e1 60%, var(--paper-dark) 100%);
    box-shadow: 0 6px 18px rgba(0,0,0,.28);
  }
  .flyer--front { left: 60px; }
  .flyer--back { left: 620px; }

  .hand { font-family: "Amatic SC", "Arial Narrow", sans-serif; font-weight: 700; line-height: .98; color: var(--ink); }
  .hand .accent { color: var(--green); }

  /* Front */
  .topic-bar {
    position: absolute; top: 0; left: 0; right: 0; height: 48px; background: var(--band);
    color: var(--white); font-weight: 900; font-size: 19px; letter-spacing: 3px;
    display: flex; align-items: center; justify-content: center; gap: 12px;
  }
  .topic-bar .accent { color: var(--lime); }
  .topic-bar .divider { font-weight: 400; color: #bbb; }

  .photo-food {
    position: absolute; top: 48px; left: 0; width: 190px; height: 690px;
    background: linear-gradient(170deg, #f2f2f2 0%, #d9dfcf 20%, #a9d040 38%, #7fbf3a 55%, #d7dccf 72%, #e6e6e6 100%);
  }
  .headline { position: absolute; top: 92px; left: 200px; width: 310px; font-size: 78px; }

  .photo-coach {
    position: absolute; left: 320px; top: 470px; width: 200px; height: 570px;
    background: linear-gradient(180deg, #d8d2cc 0%, #c9b8a7 22%, #f4f4f2 40%, #eeeeec 75%, #2a3244 88%, #222a38 100%);
  }
  .quote { position: absolute; left: 48px; top: 770px; width: 290px; font-size: 52px; }
  .signature { position: absolute; left: 150px; top: 946px; font-weight: 700; font-size: 22px; }
  .credentials { position: absolute; left: 128px; top: 978px; width: 190px; text-align: center; font-size: 11.5px; line-height: 1.3; color: var(--ink-soft); }

  /* Back */
  .photo-fresh {
    position: absolute; top: 0; right: 0; width: 200px; height: 270px;
    background: radial-gradient(circle at 40% 30%, #8cc63f 0%, #6fae2e 30%, #cfd7d4 62%, rgba(230,230,229,0) 85%);
  }
  .focus-list { position: absolute; top: 62px; left: 80px; list-style: none; }
  .focus-list li { display: flex; align-items: center; gap: 12px; font-weight: 700; font-size: 24px; margin-bottom: 6px; }
  .focus-list svg { width: 24px; height: 24px; flex: none; }

  .services { position: absolute; top: 270px; left: 76px; width: 360px; }
  .services h2 { color: var(--green); font-weight: 900; font-size: 22px; margin-bottom: 4px; }
  .services ul { padding-left: 18px; font-size: 15px; line-height: 1.26; color: var(--ink-soft); }

  .cta { position: absolute; top: 592px; left: 0; right: 0; text-align: center; font-size: 82px; }

  .contact { position: absolute; top: 696px; left: 0; right: 0; text-align: center; font-size: 21px; line-height: 1.6; color: var(--ink-soft); }
  .contact b { color: var(--green); font-weight: 900; }
  .contact .note { font-size: 14px; font-weight: 700; color: var(--ink); margin-top: 6px; line-height: 1.3; }

  .brand-band {
    position: absolute; bottom: 0; left: 0; right: 0; height: 206px; background: var(--band);
    display: flex; flex-direction: column; align-items: center; justify-content: center; gap: 26px;
  }
  .brand { display: flex; align-items: center; gap: 12px; color: #cfcfcf; font-weight: 900; font-size: 28px; letter-spacing: 1px; }
  .brand .dot { width: 34px; height: 34px; border-radius: 50%; background: var(--lime); }
  .website { color: var(--white); font-size: 22px; }
</style>
</head>
<body>
  <section class="flyer flyer--front">
    <div class="topic-bar">
      <span>Health</span><span class="divider">|</span><span class="accent">Nutrition</span><span class="divider">|</span><span>Lifestyle</span>
    </div>
    <div class="photo-food" role="img" aria-label="Healthy food, green apples, water bottle, tape measure and running shoe"></div>
    <h1 class="headline hand">"Be your best through <span class="accent">food and lifestyle</span> changes."</h1>
    <div class="photo-coach" role="img" aria-label="Portrait of the health coach in a white top, arms crossed"></div>
    <p class="quote hand">"Can help, I'm a qualified holistic <span class="accent">health coach."</span></p>
    <p class="signature">— Clara Benson</p>
    <p class="credentials">BA in Sport and<br>Exercise Management,<br>M Pharmacy</p>
  </section>

  <section class="flyer flyer--back">
    <div class="photo-fresh" role="img" aria-label="Green apples and a water bottle"></div>
    <ul class="focus-list">
      <li><svg viewBox="0 0 24 24"><rect x="2" y="6" width="15" height="15" fill="none" stroke="#555" stroke-width="1.8"/><path d="M5 12 l5 5 L22 3" fill="none" stroke="#c8202a" stroke-width="3.4" stroke-linecap="round"/></svg>Nutritional Advice</li>
      <li><svg viewBox="0 0 24 24"><rect x="2" y="6" width="15" height="15" fill="none" stroke="#555" stroke-width="1.8"/><path d="M5 12 l5 5 L22 3" fill="none" stroke="#c8202a" stroke-width="3.4" stroke-linecap="round"/></svg>Fitness Planning</li>
      <li><svg viewBox="0 0 24 24"><rect x="2" y="6" width="15" height="15" fill="none" stroke="#555" stroke-width="1.8"/><path d="M5 12 l5 5 L22 3" fill="none" stroke="#c8202a" stroke-width="3.4" stroke-linecap="round"/></svg>Natural Health Management</li>
      <li><svg viewBox="0 0 24 24"><rect x="2" y="6" width="15" height="15" fill="none" stroke="#555" stroke-width="1.8"/><path d="M5 12 l5 5 L22 3" fill="none" stroke="#c8202a" stroke-width="3.4" stroke-linecap="round"/></svg>Lifestyle Assessment</li>
    </ul>

    <div class="services">
      <h2>My services:</h2>
      <ul>
        <li>Holistic Health Check-up</li>
        <li>Weight-loss goals</li>
        <li>Mini Medication Reviews</li>
        <li>Review of Vitamins and Supplements</li>
        <li>Nutritional Guidance</li>
        <li>Exercise Guidance</li>
        <li>Use of Natural Therapies</li>
        <li>Sleep Management</li>
        <li>Stress Management</li>
        <li>Specific Health Concerns</li>
        <li>Long Term Disease Management</li>
        <li>Food Tips and Education</li>
      </ul>
    </div>

    <h2 class="cta hand">Get started now!</h2>

    <div class="contact">
      <p>Contact <b>Clara Benson</b></p>
      <p><b>Phone:</b> (02) 5550 1234</p>
      <p><b>Mobile:</b> 0400 555 123</p>
      <p><b>Email:</b> clara@brightpathnotes.com.au</p>
      <p class="note">Home consultations available.</p>
    </div>

    <footer class="brand-band">
      <div class="brand"><span class="dot"></span><span>BRIGHT PATH NOTES</span></div>
      <p class="website">www.brightpathnotes.com.au</p>
    </footer>
  </section>
</body>
</html>
```